TA BRAMLEY BUSINESS CARD DESIGN PROJECT

We need to utilize our logo that was expertly created on PixelHarbor and now need to match this with a business card design.

```html
<!DOCTYPE html>
<html lang="en">
<head>
<meta charset="utf-8">
<title>TA Bramley Business Card</title>
<link href="https://fonts.googleapis.com/css2?family=Montserrat:wght@500;600;800&display=swap" rel="stylesheet">
<style>
  :root {
    --brand-blue: #1158ab;
    --card-black: #141414;
    --card-white: #ffffff;
    --canvas-bg: #e4e5e8;
    --text-light: #f2f2f2;
  }
  * { margin: 0; padding: 0; box-sizing: border-box; }
  html, body { width: 1200px; height: 900px; overflow: hidden; }
  body {
    background: var(--canvas-bg);
    font-family: "Montserrat", sans-serif;
    position: relative;
  }
  .card {
    position: absolute;
    left: 320px;
    width: 560px;
    height: 320px;
    border-radius: 22px;
    overflow: hidden;
    box-shadow: 0 10px 30px rgba(0,0,0,0.18);
  }
  .card-front {
    top: 100px;
    background: var(--brand-blue);
    display: flex;
    align-items: center;
    justify-content: center;
  }
  .card-back { top: 470px; background: var(--card-white); }
  .wordmark {
    display: flex;
    align-items: center;
    gap: 16px;
    font-weight: 800;
    letter-spacing: 0.12em;
    white-space: nowrap;
  }
  .wordmark-mark { width: 26px; height: 26px; border-radius: 50%; flex: none; }
  .card-front .wordmark { color: var(--card-white); font-size: 50px; }
  .card-front .wordmark-mark { background: var(--card-white); }
  .card-back .wordmark {
    position: absolute;
    left: 32px;
    top: 92px;
    gap: 12px;
    color: var(--brand-blue);
    font-size: 23px;
    letter-spacing: 0.1em;
  }
  .card-back .wordmark-mark { background: var(--brand-blue); width: 16px; height: 16px; }
  .back-shapes { position: absolute; inset: 0; width: 560px; height: 320px; }
  .contact {
    position: absolute;
    right: 26px;
    top: 44px;
    text-align: right;
    color: var(--text-light);
    font-weight: 500;
    font-size: 12.5px;
    line-height: 1.55;
  }
  .contact-name {
    color: var(--brand-blue);
    font-weight: 800;
    font-size: 19px;
    letter-spacing: 0.02em;
    line-height: 1.1;
  }
  .contact-title { font-size: 13px; margin-bottom: 14px; }
  .contact-row { display: flex; justify-content: flex-end; align-items: center; gap: 8px; }
  .contact-row svg { width: 11px; height: 11px; fill: var(--brand-blue); }
  .contact-group { margin-bottom: 12px; }
  .name-bar {
    position: absolute;
    right: 0;
    top: 40px;
    width: 8px;
    height: 40px;
    background: var(--brand-blue);
  }
</style>
</head>
<body>
  <section class="card card-front">
    <div class="wordmark"><span class="wordmark-mark"></span>TA BRAMLEY</div>
  </section>

  <section class="card card-back">
    <svg class="back-shapes" viewBox="0 0 560 320" aria-hidden="true">
      <path fill="var(--brand-blue)" d="M398 0 L560 0 L560 320 L0 320 L0 294 C134 290 196 262 244 206 C306 128 318 36 398 0 Z"/>
      <path fill="var(--card-white)" d="M412 0 L560 0 L560 320 L0 320 L0 304 C138 300 204 274 252 214 C314 136 326 40 412 0 Z"/>
      <path fill="var(--card-black)" d="M420 0 L560 0 L560 320 L0 320 L0 312 C142 308 210 282 260 220 C322 142 334 42 420 0 Z"/>
    </svg>
    <div class="name-bar"></div>
    <div class="wordmark"><span class="wordmark-mark"></span>TA BRAMLEY</div>
    <div class="contact">
      <div class="contact-name">COLIN MARSH</div>
      <div class="contact-title">Managing Director</div>
      <div class="contact-group">
        <div class="contact-row">123 456 789
          <svg viewBox="0 0 12 12"><path d="M2 1h3l1 3-2 1a6 6 0 0 0 3 3l1-2 3 1v3c0 1-1 1-1 1A10 10 0 0 1 1 2s0-1 1-1z"/></svg>
        </div>
        <div class="contact-row">123 456 789
          <svg viewBox="0 0 12 12"><path d="M3 0h6a1 1 0 0 1 1 1v10a1 1 0 0 1-1 1H3a1 1 0 0 1-1-1V1a1 1 0 0 1 1-1zm0 2v7h6V2z"/></svg>
        </div>
      </div>
      <div class="contact-group">
        <div class="contact-row">info@yourmail.com
          <svg viewBox="0 0 12 12"><path d="M0 2h12v8H0zm1 1v.3l5 3.2 5-3.2V3z"/></svg>
        </div>
        <div class="contact-row">www.yourwebsite.com
          <svg viewBox="0 0 12 12"><circle cx="6" cy="6" r="6"/></svg>
        </div>
      </div>
      <div>Your address, City<br>State, Zip 1234</div>
    </div>
  </section>
</body>
</html>
```